Beacon Advisory Website

I currently have a website www.beaconadvisoryinc.com. We are a IT Consulting Company. Our website will pretty much tell out our services. I am looking to enhance my website and make it look more professional. Looking for very classy and Contemporary look and design for my website.

It Company

```html
<!DOCTYPE html>
<html lang="en">
<head>
<meta charset="utf-8">
<title>Beacon Advisory</title>
<link href="https://fonts.googleapis.com/css2?family=Ubuntu:wght@400;500;700&family=Arimo:wght@400;700&display=swap" rel="stylesheet">
<style>
:root{
  --blue:#0e7cc1;
  --blue-dark:#0a5f9e;
  --ink:#222;
  --grey-text:#9a9a9a;
  --dark-panel:#3a3a3a;
  --light-panel:#efefef;
  --page-bg:#f1f2f4;
  --white:#fff;
  --black:#050505;
}
*{box-sizing:border-box;margin:0;padding:0}
html,body{width:1200px;height:3285px;overflow:hidden}
body{background:var(--page-bg);font-family:"Arimo",Arial,sans-serif;color:var(--ink);position:relative}
.abs{position:absolute}
.sheet{position:absolute;left:77px;top:77px;width:1048px;height:3137px;background:var(--white);border:1px solid #dedede}
.h{font-family:"Ubuntu",Arial,sans-serif}

/* header */
.brand{left:96px;top:110px;display:flex;align-items:center;gap:12px}
.brand-mark{width:40px;height:40px;background:var(--blue)}
.brand-name{font-family:"Ubuntu",sans-serif;font-weight:700;font-size:30px;color:var(--blue);text-transform:uppercase;letter-spacing:.5px}
.social{top:90px;width:44px;height:44px;border-radius:50%;background:var(--blue)}
.contact-line{top:148px;right:88px;display:flex;gap:26px;font-size:15px;color:var(--blue);align-items:center}
.contact-line span{display:flex;align-items:center;gap:9px}

/* nav */
.nav{left:90px;top:197px;width:1022px;height:60px;background:var(--blue);display:flex}
.nav a{font-family:"Ubuntu",sans-serif;color:#fff;font-size:15px;text-decoration:none;display:flex;align-items:center;justify-content:center;border-right:1px solid rgba(255,255,255,.18)}
.nav a.active{background:var(--blue-dark)}
.nav .search{position:absolute;right:16px;top:16px}

/* hero */
.hero{left:90px;top:257px;width:1022px;height:568px;overflow:hidden}
.hero-photo{position:absolute;inset:0;background:linear-gradient(115deg,#e9f4fa 0%,#bfe2f3 35%,#9ed3ee 60%,#d8eef8 100%)}
.hero-figure{position:absolute;right:0;top:60px;width:470px;height:508px;background:linear-gradient(180deg,#c7dfea 0%,#8aa7b6 55%,#3a4450 100%);opacity:.55}
.hero-title{position:absolute;left:22px;top:190px;font-family:"Ubuntu",sans-serif;font-size:57px;color:#1d1d1d;letter-spacing:.5px}
.hero-sub{position:absolute;left:26px;top:270px;width:560px;font-family:"Ubuntu",sans-serif;font-size:24px;line-height:31px;color:#1d1d1d}
.btn-outline-dark{position:absolute;left:22px;top:353px;width:186px;height:61px;border:2px solid #1d1d1d;font-family:"Ubuntu",sans-serif;font-size:20px;display:flex;align-items:center;justify-content:center;color:#1d1d1d}

/* features */
.features{left:90px;top:825px;width:1022px;height:397px;background:var(--dark-panel);display:flex}
.feature{flex:1;position:relative;text-align:center;color:#fff;border-right:1px dashed #6a6a6a}
.feature:last-child{border-right:0}
.feature-ring{position:absolute;left:50%;top:62px;width:124px;height:124px;margin-left:-62px;border-radius:50%;border:2px solid #cfcfcf;display:flex;align-items:center;justify-content:center}
.feature-ring.blue{border-color:var(--blue)}
.feature-dot{width:104px;height:104px;border-radius:50%;background:#fff;display:flex;align-items:center;justify-content:center}
.feature-ring.blue .feature-dot{background:var(--blue)}
.feature-note{position:absolute;left:0;right:0;top:190px;font-size:13px;color:#8c8c8c}
.feature h3{position:absolute;left:0;right:0;top:218px;font-family:"Ubuntu",sans-serif;font-weight:400;font-size:21px;letter-spacing:.5px}
.feature p{position:absolute;left:30px;right:30px;top:258px;font-size:14.5px;line-height:27px;color:#e8e8e8}
.feature p b{font-weight:400;color:var(--blue)}

/* about */
.about-shot{left:90px;top:1316px;width:401px;height:278px;background:linear-gradient(120deg,#dff0f9,#a9d8f0 60%,#e5f2f9);border:14px solid #151515;border-bottom-width:20px}
.about-stand{left:240px;top:1594px;width:100px;height:50px;background:linear-gradient(#d4d4d4,#9a9a9a)}
.eyebrow{font-family:"Ubuntu",sans-serif;color:var(--blue);font-size:24px}
.section-title{font-family:"Ubuntu",sans-serif;color:var(--blue);font-size:42px;font-weight:500;letter-spacing:.5px}
.about-text{left:518px;top:1383px;width:590px;font-size:14.5px;line-height:27.5px;color:var(--grey-text)}
.btn-solid{background:var(--blue);color:#fff;font-family:"Ubuntu",sans-serif;display:flex;align-items:center;justify-content:center}
.btn-line{border:2px solid var(--blue);color:var(--blue);font-family:"Ubuntu",sans-serif;display:flex;align-items:center;justify-content:center;background:#fff}

/* services */
.services{left:90px;top:1703px;width:1022px;height:645px;background:var(--light-panel)}
.service{position:absolute;top:194px;width:262px;text-align:center}
.service-icon{width:106px;height:106px;border-radius:50%;background:#fff;margin:0 auto;display:flex;align-items:center;justify-content:center}
.service-icon.on{background:var(--blue)}
.service h4{margin-top:30px;font-family:"Ubuntu",sans-serif;font-weight:400;font-size:16px;color:var(--blue)}
.service p{margin-top:12px;font-size:14px;line-height:25px;color:#777}
.service .btn{margin:14px auto 0;width:136px;height:50px;font-size:16px}

/* team & news */
.team-photo{top:2488px;width:156px;height:206px;border:2px solid var(--blue);background:linear-gradient(180deg,#eef2f5,#c3ccd4 60%,#6f7883)}
.team-text{top:2715px;width:158px;font-size:14px;line-height:25px;color:#999}
.team-btn{top:2859px;width:103px;height:61px;font-size:20px}
.news{left:641px;width:456px}
.news-num{position:absolute;left:0;top:0;font-family:"Ubuntu",sans-serif;font-size:48px;line-height:48px;color:#111}
.news-month{position:absolute;left:0;top:52px;font-family:"Ubuntu",sans-serif;font-size:23px;color:#111}
.news-title{position:absolute;left:85px;top:-2px;font-family:"Ubuntu",sans-serif;font-size:23px;color:var(--blue)}
.news-text{position:absolute;left:85px;top:34px;width:370px;font-size:14px;line-height:28px;color:#999}
.news-rule{position:absolute;left:85px;top:108px;width:367px;border-top:1px dashed #8a8a8a}

/* footer */
.footer{left:90px;top:2984px;width:1022px;height:158px;background:var(--blue);color:#fff;font-size:14.5px}
.foot-item{position:absolute;top:50px;display:flex;align-items:center;gap:22px;line-height:27px}
.foot-badge{width:56px;height:56px;border-radius:50%;background:#fff;display:flex;align-items:center;justify-content:center;flex:none}
.foot-div{position:absolute;top:36px;width:1px;height:90px;background:rgba(255,255,255,.7)}
.copyright{left:90px;top:3142px;width:1022px;height:61px;background:var(--black);color:#fff;font-size:14px;display:flex;align-items:center;justify-content:center}
.copyright b{font-weight:400;color:var(--blue);margin:0 4px}
</style>
</head>
<body>
<div class="sheet"></div>

<header>
  <div class="abs brand"><div class="brand-mark"></div><div class="brand-name">Beacon Advisory</div></div>
  <div class="abs social" style="left:948px"></div>
  <div class="abs social" style="left:1007px"></div>
  <div class="abs social" style="left:1066px"></div>
  <div class="abs contact-line">
    <span><svg width="20" height="20" viewBox="0 0 24 24"><path fill="#0e7cc1" d="M6.6 10.8a15 15 0 006.6 6.6l2.2-2.2c.3-.3.7-.4 1-.2 1.1.4 2.3.6 3.6.6.6 0 1 .4 1 1V20c0 .6-.4 1-1 1A17 17 0 013 4c0-.6.4-1 1-1h3.5c.6 0 1 .4 1 1 0 1.3.2 2.5.6 3.6.1.3 0 .7-.2 1z"/></svg>+1 (555) 014 2290 FREE</span>
    <span><svg width="24" height="18" viewBox="0 0 24 18"><rect width="24" height="18" rx="2" fill="#0e7cc1"/><path d="M2 3l10 7 10-7" stroke="#fff" stroke-width="2" fill="none"/></svg>Mail id: careers@beaconadvisory.com</span>
  </div>
  <nav class="abs nav">
    <a class="active" style="width:136px">COMPANY</a>
    <a style="width:136px">SERVICES</a>
    <a style="width:136px">SOLUTION</a>
    <a style="width:136px">RESOURCES</a>
    <a style="width:118px">CAREER</a>
    <a style="width:147px">CONTACT US</a>
    <svg class="search" width="28" height="28" viewBox="0 0 24 24"><circle cx="10" cy="10" r="6.5" stroke="#fff" stroke-width="2.6" fill="none"/><path d="M15 15l6 6" stroke="#fff" stroke-width="3" stroke-linecap="round"/></svg>
  </nav>
</header>

<section class="abs hero">
  <div class="hero-photo" role="img" aria-label="Bright blue office backdrop"></div>
  <div class="hero-figure" role="img" aria-label="Photo of a consultant working on a laptop"></div>
  <h1 class="hero-title">BEACON ADVISORY</h1>
  <p class="hero-sub">We provide unique and tailored solutions for various industries!</p>
  <div class="btn-outline-dark">CONTACT NOW</div>
</section>

<section class="abs features">
  <div class="feature">
    <div class="feature-ring blue"><div class="feature-dot">
      <svg width="44" height="36" viewBox="0 0 44 36"><rect x="4" y="16" width="36" height="5" fill="#fff"/><rect x="9" y="21" width="3" height="12" fill="#fff"/><rect x="32" y="21" width="3" height="12" fill="#fff"/><rect x="14" y="4" width="16" height="10" fill="#fff"/></svg>
    </div></div>
    <h3>CONSULTING</h3>
    <p>Beacon Advisory has certified professional consultants to work with you to help increase the business by ... <b>READ MORE</b></p>
  </div>
  <div class="feature">
    <div class="feature-ring"><div class="feature-dot">
      <svg width="44" height="40" viewBox="0 0 44 40"><rect x="6" y="6" width="32" height="22" fill="none" stroke="#7a8a99" stroke-width="2.5"/><path d="M12 22l7-7 5 5 8-9" stroke="#0e7cc1" stroke-width="2.5" fill="none"/><path d="M22 28v8M14 36h16" stroke="#7a8a99" stroke-width="2.5"/></svg>
    </div></div>
    <div class="feature-note">Lorem ipsum dolor sit amet,</div>
    <h3>STAFF AUGMENTION</h3>
    <p>For years Beacon Advisory as been offering our customers the ability to augment their existing staff ...<b>READ MORE</b></p>
  </div>
  <div class="feature">
    <div class="feature-ring"><div class="feature-dot">
      <svg width="40" height="44" viewBox="0 0 40 44"><path d="M20 8a11 11 0 00-6 20v5h12v-5a11 11 0 00-6-20z" fill="none" stroke="#0e7cc1" stroke-width="2.5"/><path d="M15 37h10M17 41h6M20 1v3M5 8l2 2M35 8l-2 2" stroke="#0e7cc1" stroke-width="2.5"/></svg>
    </div></div>
    <h3>OFFSHORE</h3>
    <p>Our Offshore development model has a unique distinction of providing efficient software solutions... <b>READ MORE</b></p>
  </div>
</section>

<section>
  <div class="abs about-shot" role="img" aria-label="Preview of the website shown on a desktop monitor"></div>
  <div class="abs about-stand"></div>
  <div class="abs eyebrow" style="left:518px;top:1284px">ABOUT</div>
  <h2 class="abs section-title" style="left:516px;top:1318px">BEACON ADVISORY</h2>
  <p class="abs about-text">Today's IT market is a dynamic, fast-paced industry, with ever-increasing demands. Meeting these demands for over 25 years, Beacon Advisory maintains a global presence, aggressively recruiting expertly qualified IT and Management Professionals from around the world and cultivating key partnerships with corporations to understand their business models end-to-end, with a goal of delivering exceptional client service and ensuring a consistent delivery of the talent needed to drive results...</p>
  <div class="abs btn-solid" style="left:518px;top:1566px;width:167px;height:60px;font-size:19px">KNOW MORE</div>
  <div class="abs btn-line" style="left:702px;top:1566px;width:160px;height:60px;font-size:19px">JOIN US</div>
</section>

<section class="abs services">
  <div class="abs eyebrow" style="left:0;right:0;top:60px;text-align:center">OUR</div>
  <h2 class="abs section-title" style="left:0;right:0;top:100px;text-align:center">SERVICES</h2>
  <div class="service" style="left:-13px">
    <div class="service-icon on"><svg width="44" height="48" viewBox="0 0 40 44"><path d="M20 8a11 11 0 00-6 20v5h12v-5a11 11 0 00-6-20z" fill="none" stroke="#fff" stroke-width="2.5"/><path d="M15 37h10M17 41h6M20 1v3M5 8l2 2M35 8l-2 2M1 20h3M36 20h3" stroke="#fff" stroke-width="2.5"/></svg></div>
    <h4>TECHNOLOGY</h4>
    <p>Beacon Advisory Training program<br>are perfect for individuals ...</p>
    <div class="btn btn-solid">READ MORE</div>
  </div>
  <div class="service" style="left:249px">
    <div class="service-icon"><svg width="44" height="40" viewBox="0 0 44 40"><rect x="4" y="26" width="6" height="10" fill="#0e7cc1"/><rect x="14" y="20" width="6" height="16" fill="#0e7cc1"/><rect x="24" y="14" width="6" height="22" fill="#0e7cc1"/><rect x="34" y="8" width="6" height="28" fill="#0e7cc1"/><path d="M4 18L16 8l8 6L38 2" stroke="#0e7cc1" stroke-width="2.5" fill="none"/></svg></div>
    <h4>BUSINESS</h4>
    <p>Beacon Advisory Training program<br>are perfect for individuals ...</p>
    <div class="btn btn-line">READ MORE</div>
  </div>
  <div class="service" style="left:510px">
    <div class="service-icon"><svg width="44" height="44" viewBox="0 0 44 44"><rect x="18" y="8" width="20" height="26" fill="none" stroke="#0e7cc1" stroke-width="2.5"/><path d="M23 20l4 4 7-8" stroke="#0e7cc1" stroke-width="2.5" fill="none"/><circle cx="12" cy="30" r="7" fill="none" stroke="#555" stroke-width="2.5"/><circle cx="12" cy="30" r="2.5" fill="#555"/></svg></div>
    <h4>IT CONSULTING</h4>
    <p>Beacon Advisory Training program<br>are perfect for individuals ...</p>
    <div class="btn btn-line">READ MORE</div>
  </div>
  <div class="service" style="left:773px">
    <div class="service-icon"><svg width="42" height="42" viewBox="0 0 42 42"><g fill="#0e7cc1"><rect x="2" y="2" width="10" height="10"/><rect x="16" y="2" width="10" height="10"/><rect x="30" y="2" width="10" height="10"/><rect x="2" y="16" width="10" height="10"/><rect x="16" y="16" width="10" height="10"/><rect x="30" y="16" width="10" height="10"/><rect x="2" y="30" width="10" height="10"/><rect x="16" y="30" width="10" height="10"/><rect x="30" y="30" width="10" height="10"/></g></svg></div>
    <h4>APPLICATION</h4>
    <p>Beacon Advisory Training program<br>are perfect for individuals ...</p>
    <div class="btn btn-line">READ MORE</div>
  </div>
  <div class="abs btn-solid" style="left:432px;top:522px;width:156px;height:59px;font-size:19px">SHOW ALL</div>
</section>

<section>
  <h2 class="abs section-title" style="left:92px;top:2410px;font-size:40px">OUR TEAM</h2>
  <div class="abs team-photo" style="left:92px" role="img" aria-label="Portrait of a senior team member"></div>
  <div class="abs team-photo" style="left:263px" role="img" aria-label="Portrait of a team member"></div>
  <div class="abs team-photo" style="left:434px" role="img" aria-label="Portrait of a team member"></div>
  <p class="abs team-text" style="left:94px">Lorem ipsum dolor sit amet, consectetur adipiscing elit, sed doeiusmod tempor. Et dolore magna aliqua.</p>
  <p class="abs team-text" style="left:265px">Lorem ipsum dolor sit amet, consectetur adipiscing elit, sed doeiusmod tempor. Et dolore magna aliqua.</p>
  <p class="abs team-text" style="left:436px">Lorem ipsum dolor sit amet, consectetur adipiscing elit, sed doeiusmod tempor. Et dolore magna aliqua.</p>
  <div class="abs btn-solid team-btn" style="left:92px">MORE</div>
  <div class="abs btn-solid team-btn" style="left:267px">MORE</div>
  <div class="abs btn-solid team-btn" style="left:436px">MORE</div>

  <h2 class="abs section-title" style="left:644px;top:2410px;font-size:40px">NEWS &amp; EVENT</h2>
  <div class="abs news" style="top:2514px">
    <div class="news-num">01</div><div class="news-month">March</div>
    <div class="news-title">Lorem ipsum dolor</div>
    <p class="news-text">Lorem ipsum dolor sit amet, Lorem consectetur adipiscing elit dolor Lorem ipsum dolor sit amet,...</p>
    <div class="news-rule"></div>
  </div>
  <div class="abs news" style="top:2661px">
    <div class="news-num">02</div><div class="news-month">March</div>
    <div class="news-title">Lorem ipsum dolor</div>
    <p class="news-text">Lorem ipsum dolor sit amet, Lorem consectetur adipiscing elit dolor Lorem ipsum dolor sit amet,...</p>
    <div class="news-rule"></div>
  </div>
  <div class="abs news" style="top:2808px">
    <div class="news-num">03</div><div class="news-month">March</div>
    <div class="news-title">Lorem ipsum dolor</div>
    <p class="news-text">Lorem ipsum dolor sit amet, Lorem consectetur adipiscing elit dolor Lorem ipsum dolor sit amet,...</p>
    <div class="news-rule"></div>
  </div>
</section>

<footer>
  <div class="abs footer">
    <div class="foot-item" style="left:0"><div class="foot-badge" style="background:#111;margin-left:0"><svg width="22" height="28" viewBox="0 0 22 28"><path d="M11 1a10 10 0 00-10 10c0 7 10 16 10 16s10-9 10-16A10 10 0 0011 1z" fill="#fff"/><circle cx="11" cy="11" r="4" fill="#111"/></svg></div><div>480 Harbor Lane Suite 120<br>Westbrook, NJ 07990</div></div>
    <div class="foot-div" style="left:246px"></div>
    <div class="foot-item" style="left:246px;top:64px"><div class="foot-badge" style="margin-left:12px"><svg width="26" height="20" viewBox="0 0 24 18"><rect width="24" height="18" rx="2" fill="#111"/><path d="M2 3l10 7 10-7" stroke="#fff" stroke-width="2" fill="none"/></svg></div><div>Mail id: careers@beaconadvisory.com</div></div>
    <div class="foot-div" style="left:692px"></div>
    <div class="foot-item" style="left:702px;top:64px"><div class="foot-badge" style="margin-left:12px"><svg width="26" height="26" viewBox="0 0 24 24"><path fill="#111" d="M6.6 10.8a15 15 0 006.6 6.6l2.2-2.2c.3-.3.7-.4 1-.2 1.1.4 2.3.6 3.6.6.6 0 1 .4 1 1V20c0 .6-.4 1-1 1A17 17 0 013 4c0-.6.4-1 1-1h3.5c.6 0 1 .4 1 1 0 1.3.2 2.5.6 3.6.1.3 0 .7-.2 1z"/></svg></div><div>+1 (555) 014 2290 FREE</div></div>
  </div>
  <div class="abs copyright">© 2016. <b>BEACON ADVISORY.</b> All Rights Reserved.</div>
</footer>
</body>
</html>
```